Black Car Limousine transportation business in Naples Florida

Always stand for my reliability and RVD stands for Love, K and M are the first initials of my children's names. It should show professionalism and a dedication to customer service. We keep our clients identities private. Show our professionalism. We are Black car Black tie company. We service transportation on a reserve basis to and from residents, airports, casinos, hotels,

Target Market(s)

It is a Private car service. High end clients. Businesses, Celebrity and athletes. Service to airports, hotels, special events.

Industry/Entity Type

Business

Contact Information for Business Card

A pearl metallic or Luster card. Standard business card size. Would like the name, Company email, show we take credit cards and phone number. Currently I don't have a website but will like to add later.

Logo Text

STEADFAST RVD TRANSPORTATION

Font styles to use
Serif

Colors
eaeaea
000000

Requirements
Must have
• Must have Company email, show we take credit cards and phone number. Currently I don't have a website but will like to add later.
Nice to have
• Would like to stay with a black and white theme. Open to some color trim.
Should not have
• Open to suggestions

```html
<!DOCTYPE html>
<html lang="en">
<head>
<meta charset="utf-8">
<title>Steadfast RVD Transportation – Business Card</title>
<link rel="stylesheet" href="https://fonts.googleapis.com/css2?family=Open+Sans:ital,wght@0,400;0,600;0,700;1,700&display=swap">
<style>
  :root {
    --stage: #c4c4c4;
    --paper: #ffffff;
    --ink: #000000;
    --text: #1a1a1a;
    --muted: #3a3a3a;
    --silver: #9a9a9a;
    --stripe: #8c8c8c;
    --pearl: #eaeaea;
  }
  * { box-sizing: border-box; margin: 0; padding: 0; }
  html, body { width: 1105px; height: 1200px; overflow: hidden; }
  body {
    background: var(--stage);
    font-family: "Open Sans", Arial, sans-serif;
    position: relative;
  }
  .card {
    position: absolute;
    left: 193px;
    width: 719px;
    height: 410px;
    overflow: hidden;
    box-shadow: 0 4px 10px rgba(0,0,0,0.35);
  }
  .card--front { top: 167px; background: var(--paper); }
  .card--back  { top: 622px; background: var(--ink); }

  .vehicle-photo {
    position: absolute;
    border-radius: 10px 14px 6px 6px;
  }
  .card--front .vehicle-photo {
    left: 52px; top: 86px; width: 130px; height: 54px;
    background: linear-gradient(180deg, #3a3a3a 0%, #0d0d0d 70%, #555 100%);
  }
  .card--back .vehicle-photo {
    left: 138px; top: 178px; width: 177px; height: 72px;
    background: linear-gradient(180deg, #4a4a4a 0%, #111 70%, #666 100%);
  }

  .brand-name {
    position: absolute;
    font-weight: 700;
    color: var(--silver);
    line-height: 1.05;
    letter-spacing: 0.5px;
  }
  .card--front .brand-name { left: 194px; top: 88px; font-size: 21px; }
  .card--back .brand-name  { left: 330px; top: 180px; font-size: 29px; color: #b5b5b5; }
  .brand-name span { display: block; }

  .holder { position: absolute; left: 52px; top: 270px; }
  .holder__name { font-size: 24px; font-weight: 600; color: var(--text); letter-spacing: 0.3px; }
  .holder__role { font-size: 19px; color: var(--muted); margin-top: 0px; }

  .contact {
    position: absolute; right: 54px; top: 272px;
    text-align: right; font-size: 18px; color: var(--muted);
    line-height: 29px;
  }
  .contact__line { display: flex; align-items: center; justify-content: flex-end; gap: 8px; }
  .contact svg { width: 17px; height: 17px; fill: var(--ink); }

  .footer-trim { position: absolute; left: 0; bottom: 0; width: 719px; height: 50px; }
  .website {
    position: absolute; right: 40px; bottom: 13px;
    color: var(--paper); font-size: 18px; letter-spacing: 3px;
  }

  .payment-note {
    position: absolute; left: 0; right: 0; top: 333px;
    display: flex; justify-content: center; align-items: center; gap: 10px;
    color: var(--paper); font-size: 19px; font-weight: 700; font-style: italic;
  }
  .payment-note svg { width: 28px; height: 20px; }
</style>
</head>
<body>

<section class="card card--front">
  <div class="vehicle-photo" role="img" aria-label="Photo of a black luxury SUV"></div>
  <div class="brand-name"><span>STEADFAST RVD</span><span>TRANSPORTATION</span></div>

  <div class="holder">
    <div class="holder__name">DANIEL REYES</div>
    <div class="holder__role">CEO/Founder</div>
  </div>

  <div class="contact">
    <div class="contact__line">555 014 2270
      <svg viewBox="0 0 24 24" aria-hidden="true"><path d="M6.6 10.8c1.4 2.8 3.8 5.1 6.6 6.6l2.2-2.2c.3-.3.7-.4 1-.2 1.1.4 2.3.6 3.6.6.6 0 1 .4 1 1V20c0 .6-.4 1-1 1C10.6 21 3 13.4 3 4c0-.6.4-1 1-1h3.5c.6 0 1 .4 1 1 0 1.3.2 2.5.6 3.6.1.3 0 .7-.2 1z"/></svg>
    </div>
    <div class="contact__line">book@rvdcars.com
      <svg viewBox="0 0 24 24" aria-hidden="true"><path d="M2 5h20v14H2z"/><path d="M2 5l10 8 10-8" fill="none" stroke="#fff" stroke-width="1.6"/></svg>
    </div>
  </div>

  <svg class="footer-trim" viewBox="0 0 719 50" aria-hidden="true">
    <polygon points="0,14 400,14 393,26 0,26" fill="var(--stripe)"/>
    <polygon points="403,0 719,0 719,50 372,50" fill="var(--ink)"/>
  </svg>
  <div class="website">www.rvdcars.com</div>
</section>

<section class="card card--back">
  <div class="vehicle-photo" role="img" aria-label="Photo of a black luxury SUV"></div>
  <div class="brand-name"><span>STEADFAST RVD</span><span>TRANSPORTATION</span></div>

  <div class="payment-note">
    <svg viewBox="0 0 28 20" aria-hidden="true">
      <rect x="1" y="2" width="26" height="16" rx="3" fill="#fff"/>
      <rect x="1" y="6" width="26" height="3" fill="#000"/>
      <rect x="5" y="12" width="8" height="2" fill="#000"/>
    </svg>
    We accept credit cards
  </div>
</section>

</body>
</html>
```